Dashboard Elements

Hello – looking for someone to create dashboard elements.
I’ve already basically designed all these elements – but I need someone to take what I’ve designed and make it look like an actual dashboard UI, like an app - assuming using some kind of dashboard UI kit (but however you would like to get it done is fine). It can look just like mine or try something different, as long as it matches the color scheme webpage that I’m going to out it on – see the page here. I’m ok with making it dark, maybe that would look better – again as long as it matches the webpage (https://www.plandeck.io/file/7QxKtr2BwLpZnVe4Hs8Mc1/Webpage-with-placeholders?node-id=0%3A1). Please note, you do not need to put anything on the webpage or do anything with this Figma file, this is just a reference so you can color/stylize it accordingly.

The attached Powerpoint file has everything you need - make sure to zoom all the way out to see everything on the slides.

Here are the Dashboard elements needed (this will all make sense when you look at the PPT):
Dashboard 1
Dashboard 1 – expanded view A
Dashboard 1 – expanded view B
View Source button by itself
Source Document Viewer 1 and 2 (these are exactly the same just with a different image inside)*
Dashboard 2 (only slightly different than Dashboard 1, just extended with extra headings
Table of Contents
Searchbar and Source Doc by itself
*the documents in the source document viewers should still look like documents - they don’t need to look like part of the UI, because this is a document viewer – you can restyle/recolor if necessary or just leave these as is.
- Colors must match color scheme of webpage, attached and on Figma link (images there currently are only placeholders) – ok to go dark as long as it matches
- Must look sleek, clean, realistic
- Don’t add any pictures of people or change the text.
- In case it’s not clear, this is what I mean by the concept of Dashboard UI - https://www.notavia.net/shard/s7/sh/8fad21bc-14e9-4a7c-b2d0-5c3e9f71a604/92c4e1b7a05d3f68e1c2b947d0a3f815
- Must be sent in an editable file, I may need to be edit text and other elements
- If you are going to send a sample, please make sure it’s part of the dashboard itself, not just the table of contents etc

Ideally hoping to find someone I can continue working with as I'll have a lot more graphic design work needed coming up.

Thank you!

```html
<!DOCTYPE html>
<html lang="en">
<head>
<meta charset="utf-8">
<title>Document Viewers – Fax and Lab</title>
<link rel="stylesheet" href="https://fonts.googleapis.com/css2?family=Ubuntu:wght@400;500&family=Montserrat:wght@400;500&family=Courier+Prime&display=swap">
<style>
  :root {
    --bg-deep: #0b0916;
    --bg-mid: #15112a;
    --bg-glow: #5b3fa3;
    --violet: #7b67e2;
    --violet-soft: #8d76ea;
    --teal: #1bb8a8;
    --panel: #1b1431;
    --panel-top: #3b2a6c;
    --frame-fill: #1a1330;
    --text: #e9e6f5;
    --muted: #b7b1cf;
    --rule: #3a3256;
    --paper: #ffffff;
    --ink: #222;
  }
  * { box-sizing: border-box; margin: 0; padding: 0; }
  html, body { width: 1200px; height: 718px; overflow: hidden; }
  body {
    position: relative;
    font-family: "Montserrat", sans-serif;
    background:
      radial-gradient(ellipse 520px 300px at 180px 640px, rgba(91,63,163,.75), transparent 70%),
      radial-gradient(ellipse 700px 260px at 250px 140px, rgba(60,44,110,.55), transparent 70%),
      linear-gradient(180deg, var(--bg-mid), var(--bg-deep));
  }
  .showcase-title {
    position: absolute; top: 98px; width: 540px; text-align: center;
    font-family: "Ubuntu", sans-serif; font-weight: 500; font-size: 33px;
    color: var(--violet); letter-spacing: .3px;
  }
  .showcase-title--fax { left: 39px; }
  .showcase-title--lab { left: 607px; }

  .viewer { position: absolute; top: 218px; width: 540px; height: 328px; overflow: hidden; }
  .viewer--fax { left: 39px; }
  .viewer--lab { left: 607px; }
  .viewer-backdrop { position: absolute; inset: 0; }

  .viewer-frame {
    position: absolute; left: 28px; top: 26px; width: 488px; height: 274px;
  }
  .brand {
    position: absolute; left: 26px; top: 21px; display: flex; align-items: center; gap: 5px;
    font-family: "Montserrat", sans-serif; font-weight: 500; font-size: 11.5px;
    color: var(--text); letter-spacing: .6px;
  }
  .brand-mark { width: 10px; height: 10px; background: var(--violet); border-radius: 2px; }
  .viewer-heading {
    position: absolute; left: 147px; top: 11px;
    font-family: "Ubuntu", sans-serif; font-size: 23px; color: var(--violet-soft);
  }
  .patient { position: absolute; left: 373px; top: 17px; color: var(--text); }
  .patient-name { font-size: 9.5px; display: flex; align-items: center; gap: 6px; }
  .patient-meta { font-size: 5.6px; color: var(--muted); margin-top: 4px; }
  .patient-toggle {
    width: 8px; height: 8px; border-radius: 50%; background: var(--violet);
    display: inline-flex; align-items: center; justify-content: center;
  }
  .alert-bell { position: absolute; left: 451px; top: 16px; }

  .section-toggle {
    position: absolute; left: 117px; top: 53px; font-size: 8.6px; color: var(--text);
    display: flex; align-items: center; gap: 6px;
  }
  .section-rule { position: absolute; left: 117px; top: 79px; width: 240px; height: 1px; background: var(--rule); }

  .doc-page {
    position: absolute; left: 176px; top: 80px; width: 151px; height: 181px;
    background: var(--paper); color: var(--ink);
    font-family: "Courier Prime", monospace; font-size: 3.4px; line-height: 1.45;
    padding: 8px 9px; overflow: hidden;
  }
  .doc-page p { white-space: nowrap; }
  .doc-page .doc-gap { height: 4px; }
  .doc-page .doc-strong { font-weight: bold; font-size: 4.2px; }
  .doc-table { width: 100%; border-collapse: collapse; margin-top: 3px; }
  .doc-table td { border: .4px solid #555; padding: .5px 1.5px; font-size: 3.2px; }
  .doc-status {
    display: inline-block; border: .5px solid #444; padding: 0 8px; margin-left: 40px;
  }

  .scrollbar { position: absolute; left: 445px; top: 89px; width: 13px; height: 166px; }
  .scroll-btn {
    position: absolute; left: 0; width: 13px; height: 13px; border-radius: 50%;
    background: var(--teal); display: flex; align-items: center; justify-content: center;
  }
  .scroll-btn--up { top: 0; }
  .scroll-btn--down { bottom: 0; }
  .scroll-track {
    position: absolute; left: 3px; top: 17px; width: 7px; height: 131px;
    background: #a9a6b6; border-radius: 4px;
  }
  .scroll-thumb { position: absolute; left: 0; top: 0; width: 7px; height: 22px; background: var(--teal); border-radius: 4px; }
</style>
</head>
<body>

<h1 class="showcase-title showcase-title--fax">Document fax</h1>
<h1 class="showcase-title showcase-title--lab">Document LAB</h1>

<!-- Fax viewer -->
<section class="viewer viewer--fax">
  <svg class="viewer-backdrop" width="540" height="328" viewBox="0 0 540 328" aria-hidden="true">
    <defs>
      <linearGradient id="frameStrokeA" x1="0" y1="0" x2="1" y2="0">
        <stop offset="0" stop-color="#1bb8a8"/><stop offset=".5" stop-color="#4f7fc8"/><stop offset="1" stop-color="#8a6ff0"/>
      </linearGradient>
      <radialGradient id="tealGlowA" cx=".1" cy=".45" r=".35">
        <stop offset="0" stop-color="#1bb8a8" stop-opacity=".35"/><stop offset="1" stop-color="#1bb8a8" stop-opacity="0"/>
      </radialGradient>
      <linearGradient id="floorA" x1="0" y1="0" x2="1" y2="1">
        <stop offset="0" stop-color="#1b1431"/><stop offset="1" stop-color="#0f3a3f"/>
      </linearGradient>
    </defs>
    <rect width="540" height="328" fill="url(#floorA)"/>
    <path d="M0 0 H280 Q300 0 310 26 H540 V0 Z" fill="#2c2153"/>
    <path d="M300 0 H540 V40 H340 Q320 10 300 0 Z" fill="#3b2a6c"/>
    <ellipse cx="0" cy="200" rx="38" ry="80" fill="#1bb8a8"/>
    <ellipse cx="540" cy="190" rx="34" ry="90" fill="#7a5fd6"/>
    <ellipse cx="545" cy="280" rx="30" ry="55" fill="#1bb8a8"/>
    <rect x="28" y="26" width="488" height="274" rx="34" fill="#1a1330"/>
    <rect x="28" y="26" width="488" height="274" rx="34" fill="url(#tealGlowA)"/>
    <rect x="28" y="26" width="488" height="274" rx="34" fill="none" stroke="url(#frameStrokeA)" stroke-width="2.5"/>
  </svg>

  <div class="viewer-frame">
    <div class="brand"><span class="brand-mark"></span>CLINIVAULT</div>
    <h2 class="viewer-heading">C-CDA Compendium</h2>
    <div class="patient">
      <div class="patient-name">Patient, Mary
        <span class="patient-toggle"><svg width="5" height="4" viewBox="0 0 5 4"><path d="M.5 1 2.5 3 4.5 1" stroke="#fff" stroke-width=".9" fill="none"/></svg></span>
      </div>
      <div class="patient-meta">Female | 01/11/1951 | Age: 70</div>
    </div>
    <svg class="alert-bell" width="12" height="13" viewBox="0 0 12 13" aria-label="Notifications">
      <path d="M2 9 V5.5 A4 4 0 0 1 10 5.5 V9 L11 10 H1 Z" fill="#1bb8a8"/><circle cx="6" cy="11.4" r="1.3" fill="#1bb8a8"/><circle cx="10" cy="2" r="1.8" fill="#1bb8a8"/>
    </svg>

    <div class="section-toggle">
      <svg width="7" height="5" viewBox="0 0 7 5"><path d="M1 1 3.5 3.8 6 1" stroke="#1bb8a8" stroke-width="1.4" fill="none"/></svg>
      Documents
    </div>
    <div class="section-rule"></div>

    <article class="doc-page" aria-label="Faxed office note">
      <p class="doc-strong">Eye Care Clinic</p>
      <div class="doc-gap"></div>
      <p>PATIENT&nbsp;&nbsp;&nbsp;&nbsp;&nbsp;&nbsp;&nbsp;&nbsp;Mary Patient</p>
      <p>DATE OF BIRTH&nbsp;&nbsp;01/11/1951</p>
      <p>VISIT TYPE&nbsp;&nbsp;&nbsp;&nbsp;&nbsp;Office Visit</p>
      <div class="doc-gap"></div>
      <p class="doc-strong">History</p>
      <p>Patient reports blurred vision in the right eye.</p>
      <p>Cataract noted two years ago.</p>
      <div class="doc-gap"></div>
      <table class="doc-table">
        <tr><td>Eye</td><td>Distance</td><td>Near</td></tr>
        <tr><td>OD</td><td>20/40</td><td>J2</td></tr>
        <tr><td>OS</td><td>20/30</td><td>J1</td></tr>
      </table>
    </article>

    <div class="scrollbar">
      <span class="scroll-btn scroll-btn--up"><svg width="6" height="4" viewBox="0 0 6 4"><path d="M.5 3.5 3 .8 5.5 3.5Z" fill="#fff"/></svg></span>
      <div class="scroll-track"><div class="scroll-thumb"></div></div>
      <span class="scroll-btn scroll-btn--down"><svg width="6" height="4" viewBox="0 0 6 4"><path d="M.5 .5 3 3.2 5.5 .5Z" fill="#fff"/></svg></span>
    </div>
  </div>
</section>

<!-- Lab viewer -->
<section class="viewer viewer--lab">
  <svg class="viewer-backdrop" width="540" height="328" viewBox="0 0 540 328" aria-hidden="true">
    <defs>
      <linearGradient id="frameStrokeB" x1="0" y1="0" x2="1" y2="0">
        <stop offset="0" stop-color="#1bb8a8"/><stop offset=".5" stop-color="#4f7fc8"/><stop offset="1" stop-color="#8a6ff0"/>
      </linearGradient>
      <radialGradient id="tealGlowB" cx=".1" cy=".45" r=".35">
        <stop offset="0" stop-color="#1bb8a8" stop-opacity=".35"/><stop offset="1" stop-color="#1bb8a8" stop-opacity="0"/>
      </radialGradient>
      <linearGradient id="floorB" x1="0" y1="0" x2="1" y2="1">
        <stop offset="0" stop-color="#1b1431"/><stop offset="1" stop-color="#0f3a3f"/>
      </linearGradient>
    </defs>
    <rect width="540" height="328" fill="url(#floorB)"/>
    <path d="M0 0 H280 Q300 0 310 26 H540 V0 Z" fill="#2c2153"/>
    <path d="M300 0 H540 V40 H340 Q320 10 300 0 Z" fill="#3b2a6c"/>
    <ellipse cx="0" cy="200" rx="38" ry="80" fill="#1bb8a8"/>
    <ellipse cx="540" cy="190" rx="34" ry="90" fill="#7a5fd6"/>
    <ellipse cx="545" cy="280" rx="30" ry="55" fill="#1bb8a8"/>
    <rect x="28" y="26" width="488" height="274" rx="34" fill="#1a1330"/>
    <rect x="28" y="26" width="488" height="274" rx="34" fill="url(#tealGlowB)"/>
    <rect x="28" y="26" width="488" height="274" rx="34" fill="none" stroke="url(#frameStrokeB)" stroke-width="2.5"/>
  </svg>

  <div class="viewer-frame">
    <div class="brand"><span class="brand-mark"></span>CLINIVAULT</div>
    <h2 class="viewer-heading">C-CDA Compendium</h2>
    <div class="patient">
      <div class="patient-name">Patient, Mary
        <span class="patient-toggle"><svg width="5" height="4" viewBox="0 0 5 4"><path d="M.5 1 2.5 3 4.5 1" stroke="#fff" stroke-width=".9" fill="none"/></svg></span>
      </div>
      <div class="patient-meta">Female | 01/11/1951 | Age: 70</div>
    </div>
    <svg class="alert-bell" width="12" height="13" viewBox="0 0 12 13" aria-label="Notifications">
      <path d="M2 9 V5.5 A4 4 0 0 1 10 5.5 V9 L11 10 H1 Z" fill="#1bb8a8"/><circle cx="6" cy="11.4" r="1.3" fill="#1bb8a8"/><circle cx="10" cy="2" r="1.8" fill="#1bb8a8"/>
    </svg>

    <div class="section-toggle">
      <svg width="7" height="5" viewBox="0 0 7 5"><path d="M1 1 3.5 3.8 6 1" stroke="#1bb8a8" stroke-width="1.4" fill="none"/></svg>
      Documents
    </div>
    <div class="section-rule"></div>

    <article class="doc-page" aria-label="Lab report">
      <p><span class="doc-status">STATUS: Final</span></p>
      <p class="doc-strong">Mary Patient</p>
      <p>DOB 01/11/1951</p>
      <table class="doc-table">
        <tr><td>Test</td><td>Result</td><td>Range</td><td>Unit</td></tr>
        <tr><td>Monocytes</td><td>0.6</td><td>0.1-0.9</td><td>K/uL</td></tr>
        <tr><td>Eosinophils</td><td>0.2</td><td>0.0-0.4</td><td>K/uL</td></tr>
        <tr><td>Basophils</td><td>0.1</td><td>0.0-0.2</td><td>K/uL</td></tr>
      </table>
      <div class="doc-gap"></div>
      <p><b>HEMOGLOBIN A1C</b>&nbsp;&nbsp;5.9&nbsp;&nbsp;4.8-5.6&nbsp;&nbsp;%</p>
      <p>Glucose control for adults with diabetes: 7.0</p>
      <div class="doc-gap"></div>
      <p><b>Microalbumin Creatinine Ratio, Urine</b></p>
      <p>Creatinine&nbsp;&nbsp;118.2&nbsp;&nbsp;mg/dL</p>
      <p>&nbsp;&nbsp;&nbsp;&nbsp;Normal: 0 - 29</p>
      <div class="doc-gap"></div>
      <p>Lab Interpretation&nbsp;&nbsp;&nbsp;&nbsp;&nbsp;&nbsp;Abnormal</p>
    </article>

    <div class="scrollbar">
      <span class="scroll-btn scroll-btn--up"><svg width="6" height="4" viewBox="0 0 6 4"><path d="M.5 3.5 3 .8 5.5 3.5Z" fill="#fff"/></svg></span>
      <div class="scroll-track"><div class="scroll-thumb"></div></div>
      <span class="scroll-btn scroll-btn--down"><svg width="6" height="4" viewBox="0 0 6 4"><path d="M.5 .5 3 3.2 5.5 .5Z" fill="#fff"/></svg></span>
    </div>
  </div>
</section>

</body>
</html>
```